One piece Trade show banner, 8' x 8' square

One piece banner for trade show
8' x 8' airborne geophysical company

Target Market(s)

Business

Industry/Entity Type

mineral exploration and science

Colors
0054AA
0677BA
7BADD7
CADEEF
E8F1F8
FFC000
F8CF3A
FAE287
FDF2CF
FEFAEE

Requirements
Must have
• Company logo (attached), slogan (Airborne Geophysics for Discovery). We are looking for a new banner, for a standard 8 x 8' square one-piece booth. I have attached some pictures, our logo, our old banner for reference, and two examples from unrelated companies from a tradeshow that we like. If its possible I'd like to change the color of the helicopter from green to dark grey. IE, keep the orange and white, just change green to dark grey. Looking for a simple, clean design with minimal text.
Nice to have
• I have attached examples of banners that we like (2xIMG), plus our old 3-piece banner r.
Should not have
• Green in the helicopter. Please change the color of the helicopter with green/orange/white to dark grey/orange/white. IE change the green to dark grey and leave the orange and white alone. I've attached lots of pictures but I don't expect them all to be used.

```html
<!DOCTYPE html>
<html lang="en">
<head>
<meta charset="utf-8">
<title>Meridian AeroSurveys – Trade Show Banner</title>
<link rel="stylesheet" href="https://fonts.googleapis.com/css2?family=Poppins:wght@400;500;600;800&display=swap">
<style>
  :root {
    --brand-yellow: #FFC000;
    --brand-yellow-light: #F8CF3A;
    --brand-yellow-pale: #FAE287;
    --ink: #1c1c1c;
    --night: #0b0b0b;
    --white: #ffffff;
    --sky: #E8F1F8;
    --haze: #CADEEF;
    --mountain: #7BADD7;
    --mountain-deep: #0677BA;
    --meadow: #5f8f3e;
    --page: #f6f6f8;
  }
  * { margin: 0; padding: 0; box-sizing: border-box; }
  html, body {
    width: 1010px;
    height: 1200px;
    overflow: hidden;
    background: var(--page);
    font-family: "Poppins", sans-serif;
  }
  .banner {
    position: absolute;
    left: 15px;
    top: 110px;
    width: 980px;
    height: 980px;
    background: var(--night);
    overflow: hidden;
  }
  .hero-photo {
    position: absolute;
    left: 0;
    top: 0;
    width: 980px;
    height: 760px;
    background:
      linear-gradient(to bottom, rgba(11,11,11,0) 55%, rgba(11,11,11,0.85) 82%, var(--night) 100%),
      linear-gradient(to bottom, var(--sky) 0%, var(--haze) 30%, var(--mountain) 45%, #8fb6c9 55%, var(--meadow) 68%, #3d5b2c 80%, #1d2718 100%);
  }
  .header-arch {
    position: absolute;
    left: 0;
    top: 0;
    width: 980px;
    height: 210px;
  }
  .brand-name {
    position: absolute;
    left: 0;
    width: 980px;
    text-align: center;
    color: var(--ink);
    font-weight: 500;
    line-height: 1;
  }
  .brand-name--main { top: 36px; font-size: 66px; letter-spacing: 0.5px; }
  .brand-name--sub { top: 112px; font-size: 28px; padding-left: 250px; }
  .gold-rule {
    position: absolute;
    left: 60px;
    width: 860px;
    height: 2px;
    background: linear-gradient(to right, rgba(255,192,0,0), var(--brand-yellow) 20%, var(--brand-yellow) 80%, rgba(255,192,0,0));
  }
  .gold-rule--top { top: 609px; }
  .gold-rule--bottom { top: 692px; }
  .platforms {
    position: absolute;
    top: 624px;
    left: 0;
    width: 980px;
    text-align: center;
    color: var(--white);
    font-weight: 500;
    font-size: 39px;
    line-height: 52px;
    letter-spacing: 0.5px;
  }
  .platforms .dot { margin: 0 14px; }
  .slogan-main {
    position: absolute;
    top: 730px;
    left: 0;
    width: 980px;
    text-align: center;
    color: var(--brand-yellow-light);
    font-weight: 800;
    font-size: 61px;
    line-height: 1;
    letter-spacing: 0.5px;
  }
  .slogan-sub {
    position: absolute;
    top: 806px;
    left: 0;
    width: 980px;
    display: flex;
    justify-content: center;
    align-items: center;
    gap: 26px;
    color: var(--white);
    font-weight: 500;
    font-size: 60px;
    line-height: 1;
  }
  .slogan-sub .dash {
    width: 68px;
    height: 2px;
    background: var(--white);
  }
  .website {
    position: absolute;
    top: 893px;
    left: 0;
    width: 980px;
    display: flex;
    justify-content: center;
    align-items: center;
    gap: 12px;
    color: var(--white);
    font-weight: 500;
    font-size: 26px;
    letter-spacing: 1.5px;
  }
  .website svg { width: 24px; height: 24px; }
</style>
</head>
<body>
  <main class="banner">
    <div class="hero-photo" role="img" aria-label="Photo of a dark grey survey helicopter with orange and white stripes towing a sensor boom over green hills, a lake and hazy blue mountains"></div>

    <svg class="header-arch" viewBox="0 0 980 210" aria-hidden="true">
      <defs>
        <linearGradient id="archFill" x1="0" y1="0" x2="0" y2="1">
          <stop offset="0" stop-color="#FFC000"/>
          <stop offset="1" stop-color="#FFD83A"/>
        </linearGradient>
      </defs>
      <path d="M0,0 H980 V40 C880,150 700,200 490,200 C280,200 100,170 0,70 Z" fill="#ffffff" opacity="0.9"/>
      <path d="M0,0 H980 V10 C900,120 700,174 490,174 C280,174 80,120 0,10 Z" fill="url(#archFill)"/>
    </svg>

    <div class="brand-name brand-name--main">Meridian</div>
    <div class="brand-name brand-name--sub">AeroSurveys</div>

    <div class="gold-rule gold-rule--top"></div>
    <p class="platforms">Helicopter<span class="dot">•</span>Fixed Wing<span class="dot">•</span>Drone</p>
    <div class="gold-rule gold-rule--bottom"></div>

    <h1 class="slogan-main">AIRBORNE GEOPHYSICS</h1>
    <h2 class="slogan-sub"><span class="dash"></span>FOR DISCOVERY<span class="dash"></span></h2>

    <p class="website">
      <svg viewBox="0 0 24 24" fill="none" stroke="#ffffff" stroke-width="1.6" aria-hidden="true">
        <circle cx="12" cy="12" r="10"/>
        <ellipse cx="12" cy="12" rx="4.5" ry="10"/>
        <line x1="2" y1="12" x2="22" y2="12"/>
        <path d="M4 6.5 H20 M4 17.5 H20"/>
      </svg>
      www.meridianaerosurveys.com
    </p>
  </main>
</body>
</html>
```